Business Cards Needed for Innovative Healthcare Marketing Company

We are a marketing company focused on healthcare. Our company is all about rebranding yourself renewing your image and generating results. The phoenix stands for "reborn" or "rising" which we provide new brands for our clients we take their old brands and renew it with creativity and innovation. I am looking for a business card with color dimension. I have attached an example of a card I think has the look and feel of what I am trying to accomplish. I like that the card example has black and grey font colors, I like the font placement and the small logo, I really like the use of the colors on the right those are the colors of my logo. My logo is phoenix so maybe incorporating flames similar to that design. I would like the back a solid color maybe red with an opaque version of the logo and website. As a marketing company I am always open to creative liberty!

Target Market(s)

Doctors and business professionals.

Industry/Entity Type

Marketing

Contact Information for Business Card

Valcorne Health Care Marketing
Marla Tenwick- CEO
#(512)638-2974
email-marla@valcorne.com
website- valcorne.com

Font styles to use
Sans Serif

Colors
ec1f27
f37122
ffc214
fbed22
fbf289
f04a50

Requirements
Must have
• The logo and required information
Nice to have
• icons by the information
Should not have
• child like font

```html
<!DOCTYPE html>
<html lang="en">
<head>
<meta charset="utf-8">
<title>Valcorne Health Care Marketing – Business Cards</title>
<link href="https://fonts.googleapis.com/css2?family=Raleway:wght@200;300&family=Roboto+Slab:wght@400;700&display=swap" rel="stylesheet">
<style>
  :root {
    --backdrop: #d9d4cf;
    --card-core: #6c1a22;
    --card-edge: #330a0f;
    --mark-tone: #1f0c0e;
    --text-light: #ececec;
    --text-grey: #a9a0a2;
    --accent-red: #d8323a;
    --white: #ffffff;
  }
  * { margin: 0; padding: 0; box-sizing: border-box; }
  html, body { width: 1200px; height: 913px; overflow: hidden; background: var(--backdrop); }
  .canvas { position: relative; width: 1200px; height: 913px; }

  .card {
    position: absolute;
    width: 640px;
    height: 366px;
    border-radius: 4px;
    overflow: hidden;
    background: radial-gradient(ellipse at 60% 30%, var(--card-core) 0%, #4d1118 55%, var(--card-edge) 100%);
    box-shadow: 0 10px 26px rgba(0,0,0,0.35);
  }
  .card--front { left: 60px; top: 70px; }
  .card--back  { left: 500px; top: 477px; }

  .mark-area { position: absolute; }
  .card--front .mark-area { left: 50px; top: 60px; width: 240px; height: 240px; }
  .card--back .mark-area { left: 30px; top: 20px; width: 330px; height: 330px; }

  .brand { position: absolute; left: 318px; top: 116px; width: 290px; color: var(--text-light); }
  .brand__name {
    font-family: "Raleway", sans-serif;
    font-weight: 200;
    font-size: 50px;
    letter-spacing: 1px;
    line-height: 1;
    white-space: nowrap;
  }
  .brand__rule { width: 270px; height: 1px; background: var(--text-grey); margin: 10px 0 7px; }
  .brand__tagline {
    font-family: "Raleway", sans-serif;
    font-weight: 300;
    font-size: 14px;
    letter-spacing: 1.5px;
    color: var(--text-light);
    white-space: nowrap;
  }
  .brand__url {
    margin-top: 28px;
    margin-left: 60px;
    font-family: "Roboto Slab", serif;
    font-size: 20px;
    color: var(--text-grey);
    white-space: nowrap;
  }
  .brand__url em { font-style: normal; color: var(--accent-red); }

  .contact { position: absolute; left: 385px; top: 118px; width: 240px; }
  .contact__name {
    font-family: "Roboto Slab", serif;
    font-weight: 700;
    font-size: 23px;
    color: var(--white);
    white-space: nowrap;
  }
  .contact__role {
    font-family: "Roboto Slab", serif;
    font-size: 16px;
    color: var(--text-grey);
    margin-bottom: 12px;
  }
  .contact__line {
    display: flex;
    align-items: center;
    gap: 10px;
    font-family: "Roboto Slab", serif;
    font-size: 15px;
    color: var(--text-light);
    margin-top: 6px;
    white-space: nowrap;
  }
  .contact__icon { width: 20px; height: 20px; flex: none; }
</style>
</head>
<body>
<main class="canvas">

  <section class="card card--front" aria-label="Business card front">
    <svg class="mark-area" viewBox="0 0 240 240" aria-hidden="true">
      <circle cx="120" cy="120" r="114" fill="var(--mark-tone)" opacity="0.75"/>
    </svg>
    <div class="brand">
      <div class="brand__name">VALCORNE</div>
      <div class="brand__rule"></div>
      <div class="brand__tagline">HEALTHCARE MARKETING</div>
      <div class="brand__url">www.<em>valcorne</em>.com</div>
    </div>
  </section>

  <section class="card card--back" aria-label="Business card back">
    <svg class="mark-area" viewBox="0 0 330 330" aria-hidden="true">
      <circle cx="165" cy="165" r="160" fill="var(--mark-tone)" opacity="0.8"/>
    </svg>
    <div class="contact">
      <div class="contact__name">Marla TENWICK</div>
      <div class="contact__role">CEO</div>
      <div class="contact__line">
        <svg class="contact__icon" viewBox="0 0 20 20" aria-label="Phone">
          <circle cx="10" cy="10" r="10" fill="var(--white)"/>
          <path d="M6.5 5.5 L8.3 5.2 L9.2 7.6 L8 8.5 Q9 10.8 11.5 12 L12.4 10.8 L14.8 11.7 L14.5 13.5 Q9.5 14.5 6 9 Z" fill="var(--card-edge)"/>
        </svg>
        <span>(512) 638-2974</span>
      </div>
      <div class="contact__line">
        <svg class="contact__icon" viewBox="0 0 20 20" aria-label="Email">
          <circle cx="10" cy="10" r="10" fill="var(--white)"/>
          <rect x="5" y="6.5" width="10" height="7" fill="var(--card-edge)"/>
          <path d="M5 6.5 L10 10.5 L15 6.5" fill="none" stroke="var(--white)" stroke-width="1"/>
        </svg>
        <span>marla@valcorne.com</span>
      </div>
    </div>
  </section>

</main>
</body>
</html>
```